Crestline Plaque & Medal Unique Business Card Design

Recently selected a new logo design and waiting to recieve print files. I've attached image for your review. We are a trophies and awards company that provides engraving on trophies, plaques, name plates, name tags, desk sets, medals, acrylics, and signage.

We are located in Monroe, Louisiana and provide this service with computerized & laser engraving equipment.

Target Market(s)

Corporate, Sport, Church, and Special Events

Industry/Entity Type

Business

Contact Information for Business Card

I'd like to see the following list on the card: Trophies, Plaques, Name Plates, Name Tags, Desk Sets, Medals, Certificates... this is accomplished with Computerized & Laser Engraving

Colors
0555a3
ec1f27
ffffff

Requirements
Must have
• I like either single or double sided. If a design can be created with a frosted card stock I'd consider single. Must be Red, White, and Blue. Dwight Palmer - Owner, 412 W 8th Ave, Monroe, La 71208 office 318-555-0148 fax 318-555-0163 email: info@crestlineplaquemedal.example, and website: www.crestlineplaquemedal.example

```html
<!DOCTYPE html>
<html lang="en">
<head>
<meta charset="utf-8">
<title>Crestline Plaque &amp; Medal – Business Card</title>
<link rel="stylesheet" href="https://fonts.googleapis.com/css2?family=Didact+Gothic&family=Great+Vibes&display=swap">
<style>
  :root {
    --brand-blue: #0555a3;
    --brand-red: #ec1f27;
    --card-white: #ffffff;
    --stage: #e9e6e1;
    --ink-light: #f2f7fc;
  }
  * { margin: 0; padding: 0; box-sizing: border-box; }
  html, body {
    width: 1200px;
    height: 892px;
    overflow: hidden;
    background: var(--stage);
  }
  .business-card {
    position: absolute;
    left: 100px;
    top: 160px;
    width: 1000px;
    height: 572px;
    background: var(--card-white);
    box-shadow: 0 6px 22px rgba(0,0,0,0.18);
    overflow: hidden;
    font-family: "Didact Gothic", sans-serif;
  }
  .card-art { position: absolute; inset: 0; }
  .card-text {
    position: absolute;
    color: var(--ink-light);
    white-space: nowrap;
    line-height: 1.2;
  }
  .employee-name {
    left: 160px; top: 24px;
    font-family: "Great Vibes", cursive;
    font-size: 46px;
  }
  .employee-title { left: 150px; top: 88px; font-size: 18px; }
  .contact-line { font-size: 21px; letter-spacing: 0.3px; }
  .contact-office  { left: 136px; top: 128px; }
  .contact-fax     { left: 128px; top: 158px; }
  .contact-email   { left: 120px; top: 188px; }
  .contact-web     { left: 112px; top: 218px; }
  .contact-address { left: 104px; top: 248px; }
  .services-heading {
    left: 88px; top: 284px;
    font-family: "Great Vibes", cursive;
    font-size: 34px;
  }
  .service-line { font-size: 20px; }
  .service-1 { left: 76px; top: 340px; }
  .service-2 { left: 66px; top: 368px; }
  .service-3 { left: 56px; top: 396px; }
  .service-4 { left: 46px; top: 424px; }
  .brand-lockup {
    position: absolute;
    left: 560px; top: 492px;
    display: flex;
    align-items: center;
    gap: 12px;
    color: var(--brand-blue);
    font-size: 30px;
    line-height: 1;
    white-space: nowrap;
  }
  .brand-dot {
    width: 26px; height: 26px;
    border-radius: 50%;
    background: var(--brand-blue);
    flex: none;
  }
</style>
</head>
<body>
  <div class="business-card">
    <svg class="card-art" width="1000" height="572" viewBox="0 0 1000 572" aria-hidden="true">
      <defs>
        <linearGradient id="blueField" x1="0" y1="0" x2="1" y2="1">
          <stop offset="0" stop-color="#1b6fbf"/>
          <stop offset="0.5" stop-color="#3a94d4"/>
          <stop offset="1" stop-color="#0a5fae"/>
        </linearGradient>
      </defs>
      <rect class="blue-field" width="1000" height="572" fill="url(#blueField)"/>
      <path class="red-swoosh" d="M210 572 Q680 420 1000 200 L1000 262 Q720 450 300 572 Z" fill="#ec1f27"/>
      <path class="white-field" d="M290 572 Q720 438 1000 248 L1000 572 Z" fill="#ffffff"/>
    </svg>

    <div class="card-text employee-name">Dwight Palmer</div>
    <div class="card-text employee-title">Owner</div>

    <div class="card-text contact-line contact-office">Office 318-555-0148</div>
    <div class="card-text contact-line contact-fax">Fax 318-555-0163</div>
    <div class="card-text contact-line contact-email">info@crestlineplaquemedal.example</div>
    <div class="card-text contact-line contact-web">www.crestlineplaquemedal.example</div>
    <div class="card-text contact-line contact-address">412 W 8th Ave, Monroe, La 71208</div>

    <div class="card-text services-heading">Services</div>
    <div class="card-text service-line service-1">engraving on trophies, plaques,</div>
    <div class="card-text service-line service-2">medals, acrylics, and signage</div>
    <div class="card-text service-line service-3">name plates, name tags,</div>
    <div class="card-text service-line service-4">desk sets,</div>

    <div class="brand-lockup">
      <span class="brand-dot"></span>
      <span class="brand-name">Crestline Plaque &amp; Medal</span>
    </div>
  </div>
</body>
</html>
```